300 x 250 Web Ad for Porn Website

300 x 250 web ad that will appear on a porn site. Need to see 3 options, one with each of the 3 girls. Remove the background around the girls.

Underneath the girls image should read in big bold letters: High Speed Internet
Underneath in slightly smaller size: NO Credit Check

To the left of the girl: Save MONEY...

To the right of the girl: So you can buy more PORN

We want it to look very unique, raunchy, and eye catching.

Target Market(s)

Porn website

Industry/Entity Type

Internet Service Provider

Colors

Designer to choose colors to be used in the design.

Requirements
Must have
• Must stand out so people will definitely notice it.
• JPEG and PNG formats

```html
<!DOCTYPE html>
<html lang="en">
<head>
<meta charset="UTF-8">
<title>High Speed Internet – Web Ad</title>
<link href="https://fonts.googleapis.com/css2?family=Nunito:wght@900&family=Arvo:wght@700&family=Titan+One&display=swap" rel="stylesheet">
<style>
  :root {
    --page: #ffffff;
    --ad-red: #c8102e;
    --ad-pink: #e0306a;
    --ad-orange: #f2542f;
    --ad-purple: #5a1a8a;
    --ad-dark: #12060c;
    --text-white: #ffffff;
    --text-yellow: #f3ef0b;
    --headline-light: #ffd9a0;
    --headline-orange: #ff8a2a;
    --headline-deep: #ff5a14;
    --headline-edge: #2a0a0a;
    --chrome-light: #ffffff;
    --chrome-mid: #c9c9cf;
    --chrome-dark: #7b7b85;
  }
  * { margin: 0; padding: 0; box-sizing: border-box; }
  html, body { width: 1200px; height: 1192px; overflow: hidden; background: var(--page); }

  .ad {
    position: absolute;
    left: 162px; top: 232px;
    width: 876px; height: 728px;
    overflow: hidden;
    background:
      radial-gradient(ellipse 55% 45% at 85% 18%, rgba(255,110,60,.85), transparent 70%),
      radial-gradient(ellipse 45% 40% at 30% 10%, rgba(240,70,120,.8), transparent 70%),
      radial-gradient(ellipse 40% 35% at 22% 40%, rgba(120,40,170,.75), transparent 70%),
      linear-gradient(180deg, var(--ad-red) 0%, #b0183e 35%, #4a0d2a 65%, var(--ad-dark) 100%);
  }

  .model-photo {
    position: absolute;
    left: 270px; top: 0;
    width: 450px; height: 600px;
    border-radius: 45% 45% 30% 30% / 20% 20% 40% 40%;
    background: radial-gradient(ellipse at 50% 45%, #d79a78 0%, #b5562f 45%, rgba(150,30,40,.35) 75%, transparent 100%);
  }

  .tagline-left {
    position: absolute;
    left: 118px; top: 150px;
    font-family: "Nunito", sans-serif;
    font-weight: 900;
    color: var(--text-white);
    line-height: .95;
    letter-spacing: -1px;
  }
  .tagline-left .small { display: block; font-size: 40px; }
  .tagline-left .big { display: block; font-size: 38px; }

  .tagline-right {
    position: absolute;
    left: 618px; top: 128px;
    font-family: "Arvo", serif;
    font-weight: 700;
    color: var(--text-yellow);
    font-size: 33px;
    line-height: .95;
    letter-spacing: -1px;
  }
  .tagline-right span { display: block; }
  .tagline-right .indent { padding-left: 32px; }

  .headline {
    position: absolute;
    font-family: "Titan One", sans-serif;
    line-height: .85;
    transform: rotate(-4deg) skewX(-6deg);
    transform-origin: left top;
  }
  .headline span {
    display: block;
    background: linear-gradient(180deg, var(--headline-light) 0%, var(--headline-orange) 45%, var(--headline-deep) 100%);
    -webkit-background-clip: text;
    background-clip: text;
    color: transparent;
    -webkit-text-stroke: 2px var(--headline-edge);
    filter: drop-shadow(4px 4px 0 var(--headline-edge));
  }
  .headline-main { left: 60px; top: 470px; }
  .headline-main .line-high { font-size: 82px; padding-left: 60px; }
  .headline-main .line-speed { font-size: 82px; padding-left: 110px; }
  .headline-main .line-internet { font-size: 96px; }

  .headline-sub { left: 590px; top: 530px; }
  .headline-sub span {
    background: linear-gradient(180deg, var(--chrome-light) 0%, var(--chrome-mid) 50%, var(--chrome-dark) 100%);
    -webkit-background-clip: text;
    background-clip: text;
    font-size: 56px;
  }
  .headline-sub .line-credit { padding-left: 0; }
  .headline-sub .line-check { padding-left: 36px; }

  .flare {
    position: absolute;
    left: 250px; top: 566px;
    width: 560px; height: 4px;
    transform: rotate(-4deg);
    background: linear-gradient(90deg, transparent, rgba(200,120,255,.9) 40%, #ffffff 50%, rgba(200,120,255,.9) 60%, transparent);
  }
</style>
</head>
<body>
  <div class="ad">
    <div class="model-photo" role="img" aria-label="Cut-out photo of a model in red lingerie and devil horns, holding open a fur coat"></div>

    <div class="tagline-left">
      <span class="small">Save</span>
      <span class="big">MONEY...</span>
    </div>

    <div class="tagline-right">
      <span>...So you can</span>
      <span class="indent">buy more</span>
      <span class="indent">PORN</span>
    </div>

    <div class="flare"></div>

    <div class="headline headline-main">
      <span class="line-high">HIGH</span>
      <span class="line-speed">SPEED</span>
      <span class="line-internet">INTERNET</span>
    </div>

    <div class="headline headline-sub">
      <span class="line-no">NO</span>
      <span class="line-credit">CREDIT</span>
      <span class="line-check">CHECK</span>
    </div>
  </div>
</body>
</html>
```